"BREAKING NEWS!" Fitness photos needed

Hello.... We are creating our new ads for Linkpond and Glimmerly and we need some photos manipulated and text added.

We have 5 photos total that we would like to have the Headline read "Breaking News" and we'll be split testing two different quotes, so I'd like to have:

AD #1:
Breaking News - Finally! Ridgecrest Gets the Gym That Actually Delivers Results (and It's Fun!)

And then a second set on the same photos that read:

AD #2:
Breaking News - Ridgecrest Residents Ditch Boring Workouts for This Life-Changing Fitness Experience

I'd like the photos to pop and stand out, so if color corrections need to be done, please feel free.

I've attached all photos and an example photo that DOES NOT need to be the same. It's just an example I saw that caught my eye, but I feel could be done better.

Thank you!

```html
<!DOCTYPE html>
<html lang="en">
<head>
<meta charset="utf-8">
<title>Breaking News Ad Set</title>
<link rel="stylesheet" href="https://fonts.googleapis.com/css2?family=Poppins:ital,wght@1,800&family=Arimo:wght@400&display=swap">
<style>
  :root {
    --stage: #191919;
    --news-red: #e8141a;
    --news-black: #1c1c1c;
    --live-yellow: #f5c400;
    --paper: #ffffff;
    --ink: #111111;
    --label: #eeeeee;
    --gym-yellow: #e6d21c;
    --gym-grey: #9a9a98;
    --gym-floor: #3a3a3c;
    --gym-purple: #6b4a6e;
    --gym-pink: #d58bd0;
  }
  * { margin: 0; padding: 0; box-sizing: border-box; }
  html, body { width: 1200px; height: 1194px; overflow: hidden; background: var(--stage); }
  .board { position: relative; width: 1200px; height: 1194px; }
  .ad-card { position: absolute; background: var(--paper); overflow: hidden; }
  .ad-card--linkpond { width: 478px; height: 478px; left: 109px; }
  .ad-card--glimmerly { width: 430px; height: 430px; left: 667px; }
  .row-top .ad-card--linkpond { top: 76px; }
  .row-top .ad-card--glimmerly { top: 100px; }
  .row-bottom .ad-card--linkpond { top: 647px; }
  .row-bottom .ad-card--glimmerly { top: 671px; }
  .photo { position: absolute; left: 0; top: 0; width: 100%; height: 75.7%; }
  .photo--seated-press {
    background:
      linear-gradient(90deg, var(--gym-yellow) 0%, var(--gym-yellow) 26%, transparent 30%),
      linear-gradient(180deg, #c9c9c6 0%, var(--gym-grey) 55%, var(--gym-floor) 100%);
  }
  .photo--bent-row {
    background:
      linear-gradient(180deg, #d4d2d0 0%, #b9a77a 30%, #8a7f86 55%, var(--gym-purple) 78%, var(--gym-floor) 100%);
  }
  .banner { position: absolute; left: 0; top: 0; width: 100%; height: 100%; }
  .banner-headline { font-family: 'Poppins', sans-serif; font-style: italic; font-weight: 800; fill: var(--paper); }
  .banner-live { font-family: 'Poppins', sans-serif; font-style: italic; font-weight: 800; fill: var(--ink); }
  .banner-caption { font-family: 'Poppins', sans-serif; font-style: italic; font-weight: 800; fill: var(--ink); }
  .network-label {
    position: absolute; top: 573px; width: 300px; text-align: center;
    font-family: 'Arimo', sans-serif; font-size: 20px; color: var(--label); letter-spacing: 0.5px;
  }
  .network-label--linkpond { left: 198px; }
  .network-label--glimmerly { left: 732px; }
</style>
</head>
<body>
<div class="board">
  <svg width="0" height="0" style="position:absolute" aria-hidden="true">
    <defs>
      <linearGradient id="speed-left" x1="0" x2="1">
        <stop offset="0" stop-color="#fff" stop-opacity="0"/>
        <stop offset="1" stop-color="#fff"/>
      </linearGradient>
      <linearGradient id="speed-right" x1="0" x2="1">
        <stop offset="0" stop-color="#fff"/>
        <stop offset="1" stop-color="#fff" stop-opacity="0"/>
      </linearGradient>
      <g id="speed-lines-left" fill="url(#speed-left)">
        <rect x="15" y="522" width="180" height="4"/>
        <rect x="15" y="531" width="180" height="4"/>
        <rect x="15" y="540" width="180" height="4"/>
        <rect x="15" y="549" width="180" height="4"/>
        <rect x="15" y="558" width="180" height="4"/>
      </g>
      <g id="speed-lines-right" fill="url(#speed-right)">
        <rect x="483" y="594" width="272" height="4"/>
        <rect x="483" y="603" width="272" height="4"/>
        <rect x="483" y="612" width="272" height="4"/>
        <rect x="483" y="621" width="272" height="4"/>
        <rect x="483" y="630" width="272" height="4"/>
      </g>
    </defs>
  </svg>

  <section class="row-top">
    <article class="ad-card ad-card--linkpond">
      <div class="photo photo--seated-press" role="img" aria-label="Women doing seated overhead dumbbell presses on benches in a yellow and grey gym"></div>
      <svg class="banner" viewBox="0 0 770 770">
        <rect x="560" y="538" width="210" height="45" fill="var(--paper)"/>
        <polygon points="0,505 605,505 588,583 0,583" fill="var(--news-red)"/>
        <use href="#speed-lines-left"/>
        <text class="banner-headline" x="373" y="565" font-size="66" text-anchor="middle" textLength="350" lengthAdjust="spacingAndGlyphs">BREAKING</text>
        <polygon points="600,526 685,526 678,561 593,561" fill="var(--live-yellow)"/>
        <text class="banner-live" x="636" y="552" font-size="21" text-anchor="middle">LIVE</text>
        <rect x="0" y="583" width="770" height="187" fill="var(--paper)"/>
        <polygon points="175,577 770,577 770,654 158,654" fill="var(--news-black)"/>
        <text class="banner-headline" x="372" y="640" font-size="62" text-anchor="middle" textLength="205" lengthAdjust="spacingAndGlyphs">NEWS</text>
        <use href="#speed-lines-right"/>
        <text class="banner-caption" x="365" y="700" font-size="27" text-anchor="middle" textLength="485" lengthAdjust="spacingAndGlyphs">Finally! Ridgecrest Gets the Gym</text>
        <text class="banner-caption" x="365" y="733" font-size="27" text-anchor="middle" textLength="655" lengthAdjust="spacingAndGlyphs">That Actually Delivers Results (and It's Fun!)</text>
      </svg>
    </article>

    <article class="ad-card ad-card--glimmerly">
      <div class="photo photo--bent-row" role="img" aria-label="Woman doing a one-arm dumbbell row against an inclined bench in a busy group class"></div>
      <svg class="banner" viewBox="0 0 770 770">
        <rect x="560" y="538" width="210" height="45" fill="var(--paper)"/>
        <polygon points="0,505 605,505 588,583 0,583" fill="var(--news-red)"/>
        <use href="#speed-lines-left"/>
        <text class="banner-headline" x="373" y="565" font-size="66" text-anchor="middle" textLength="350" lengthAdjust="spacingAndGlyphs">BREAKING</text>
        <polygon points="600,526 685,526 678,561 593,561" fill="var(--live-yellow)"/>
        <text class="banner-live" x="636" y="552" font-size="21" text-anchor="middle">LIVE</text>
        <rect x="0" y="583" width="770" height="187" fill="var(--paper)"/>
        <polygon points="175,577 770,577 770,654 158,654" fill="var(--news-black)"/>
        <text class="banner-headline" x="372" y="640" font-size="62" text-anchor="middle" textLength="205" lengthAdjust="spacingAndGlyphs">NEWS</text>
        <use href="#speed-lines-right"/>
        <text class="banner-caption" x="365" y="700" font-size="27" text-anchor="middle" textLength="485" lengthAdjust="spacingAndGlyphs">Finally! Ridgecrest Gets the Gym</text>
        <text class="banner-caption" x="365" y="733" font-size="27" text-anchor="middle" textLength="655" lengthAdjust="spacingAndGlyphs">That Actually Delivers Results (and It's Fun!)</text>
      </svg>
    </article>

    <p class="network-label network-label--linkpond">LINKPOND</p>
    <p class="network-label network-label--glimmerly">GLIMMERLY</p>
  </section>

  <section class="row-bottom">
    <article class="ad-card ad-card--linkpond">
      <div class="photo photo--seated-press" role="img" aria-label="Women doing seated overhead dumbbell presses on benches in a yellow and grey gym"></div>
      <svg class="banner" viewBox="0 0 770 770">
        <polygon points="0,505 605,505 588,583 0,583" fill="var(--news-red)"/>
        <use href="#speed-lines-left"/>
        <text class="banner-headline" x="373" y="565" font-size="66" text-anchor="middle" textLength="350" lengthAdjust="spacingAndGlyphs">BREAKING</text>
        <rect x="0" y="583" width="770" height="187" fill="var(--paper)"/>
        <polygon points="175,577 770,577 770,654 158,654" fill="var(--news-black)"/>
        <text class="banner-headline" x="372" y="640" font-size="62" text-anchor="middle" textLength="205" lengthAdjust="spacingAndGlyphs">NEWS</text>
        <use href="#speed-lines-right"/>
        <text class="banner-caption" x="365" y="700" font-size="27" text-anchor="middle" textLength="485" lengthAdjust="spacingAndGlyphs">Finally! Ridgecrest Gets the Gym</text>
        <text class="banner-caption" x="365" y="733" font-size="27" text-anchor="middle" textLength="655" lengthAdjust="spacingAndGlyphs">That Actually Delivers Results (and It's Fun!)</text>
      </svg>
    </article>

    <article class="ad-card ad-card--glimmerly">
      <div class="photo photo--bent-row" role="img" aria-label="Woman doing a one-arm dumbbell row against an inclined bench in a busy group class"></div>
      <svg class="banner" viewBox="0 0 770 770">
        <polygon points="0,505 605,505 588,583 0,583" fill="var(--news-red)"/>
        <use href="#speed-lines-left"/>
        <text class="banner-headline" x="373" y="565" font-size="66" text-anchor="middle" textLength="350" lengthAdjust="spacingAndGlyphs">BREAKING</text>
        <rect x="0" y="583" width="770" height="187" fill="var(--paper)"/>
        <polygon points="175,577 770,577 770,654 158,654" fill="var(--news-black)"/>
        <text class="banner-headline" x="372" y="640" font-size="62" text-anchor="middle" textLength="205" lengthAdjust="spacingAndGlyphs">NEWS</text>
        <use href="#speed-lines-right"/>
        <text class="banner-caption" x="365" y="700" font-size="27" text-anchor="middle" textLength="485" lengthAdjust="spacingAndGlyphs">Finally! Ridgecrest Gets the Gym</text>
        <text class="banner-caption" x="365" y="733" font-size="27" text-anchor="middle" textLength="655" lengthAdjust="spacingAndGlyphs">That Actually Delivers Results (and It's Fun!)</text>
      </svg>
    </article>
  </section>
</div>
</body>
</html>
```